Layout for site fence advertising - length approx. 250 cm x 125 cm

The advertising will later be printed on a PVC film and used for events or on sports fields.

Main services :
Your regional contact at
Real estate and business financing
independent insurance advice

```html
<!DOCTYPE html>
<html lang="de">
<head>
<meta charset="UTF-8">
<title>Alpenblick Vermögensberatung – Bauzaunbanner</title>
<link rel="stylesheet" href="https://fonts.googleapis.com/css2?family=Open+Sans:wght@300;400;700;800&family=Montserrat:wght@500;600;700&display=swap">
<style>
  :root {
    --blue-deep: #23479a;
    --blue-mid: #2f5bb0;
    --blue-light: #4474c4;
    --pill-blue: #3560b3;
    --white: #ffffff;
    --ink: #1e1e1e;
    --swoosh-dark: #2b2b2b;
    --page: #e6e9ee;
    --icon-grey: #4a4a4a;
  }
  * { box-sizing: border-box; margin: 0; padding: 0; }
  html, body { width: 1200px; height: 900px; overflow: hidden; }
  body { background: var(--page); font-family: "Open Sans", Arial, sans-serif; position: relative; }

  .banner {
    position: absolute; left: 40px; top: 170px; width: 1120px; height: 560px;
    background: linear-gradient(160deg, var(--blue-deep) 0%, var(--blue-mid) 45%, var(--blue-light) 100%);
    overflow: hidden; box-shadow: 0 8px 24px rgba(0,0,0,.18);
  }
  .banner__shapes { position: absolute; inset: 0; }

  .headline { position: absolute; left: 40px; top: 46px; color: var(--white); line-height: 1; }
  .headline__line1 { font-size: 36px; font-weight: 300; }
  .headline__line1 strong { font-size: 50px; font-weight: 800; }
  .headline__line2 { display: block; margin-top: 6px; font-size: 62px; font-weight: 800; letter-spacing: -0.5px; }

  .brand { position: absolute; left: 620px; top: 34px; display: flex; align-items: center; color: var(--white); }
  .brand__mark { display: flex; align-items: center; gap: 10px; padding-right: 16px; }
  .brand__dot { width: 22px; height: 22px; border-radius: 50%; background: var(--white); }
  .brand__name { font-family: "Montserrat", Arial, sans-serif; font-weight: 600; font-size: 22px; }
  .brand__divider { width: 2px; height: 90px; background: var(--white); }
  .brand__text { padding-left: 14px; font-family: "Montserrat", Arial, sans-serif; }
  .brand__title { font-size: 21px; font-weight: 600; }
  .brand__claim { font-size: 14px; font-weight: 600; margin-top: 4px; }

  .services { position: absolute; left: 40px; top: 210px; display: flex; align-items: flex-start; color: var(--white); }
  .service { display: flex; flex-direction: column; align-items: center; text-align: center; font-size: 20px; font-weight: 400; line-height: 1.25; }
  .service--estate { width: 120px; }
  .service--financing { width: 170px; }
  .service--insurance { width: 240px; }
  .service__icon { width: 62px; height: 62px; border-radius: 50%; background: var(--white); display: flex; align-items: center; justify-content: center; margin-bottom: 14px; box-shadow: 2px 3px 4px rgba(0,0,0,.25); }
  .service__divider { width: 2px; height: 130px; background: rgba(255,255,255,.85); margin: 0 10px; }

  .advisor-photo {
    position: absolute; left: 820px; top: 130px; width: 300px; height: 430px;
    background: linear-gradient(180deg, #6d86b8 0%, #8c7a72 35%, #e9ecf2 62%, #2a2633 78%, #1f1c26 100%);
    border-top-left-radius: 150px 130px;
  }

  .phone-pill {
    position: absolute; left: 290px; top: 410px; width: 480px; height: 60px;
    background: var(--pill-blue); border-radius: 30px;
    display: flex; align-items: center; padding-left: 22px; gap: 12px;
    color: var(--white); font-size: 48px; font-weight: 700; letter-spacing: 0.5px;
  }
  .contacts { position: absolute; left: 150px; top: 490px; display: flex; align-items: center; gap: 20px; color: var(--ink); font-size: 21px; }
  .contact { display: flex; align-items: center; gap: 8px; white-space: nowrap; }
</style>
</head>
<body>
  <section class="banner">
    <svg class="banner__shapes" viewBox="0 0 1120 560" preserveAspectRatio="none" aria-hidden="true">
      <path d="M0 560 L0 465 C260 370 600 345 900 368 L900 560 Z" fill="var(--white)"/>
      <path d="M0 465 C260 370 600 345 900 368 C600 360 260 395 0 490 Z" fill="var(--swoosh-dark)"/>
      <path d="M0 490 C260 395 600 362 900 370 C600 375 270 420 0 520 Z" fill="var(--blue-mid)"/>
      <path d="M0 520 C270 420 600 377 880 372 C600 392 280 445 0 548 Z" fill="var(--swoosh-dark)"/>
    </svg>

    <h1 class="headline">
      <span class="headline__line1">Ihr regionaler <strong>Finanz</strong>- und</span>
      <span class="headline__line2">Versicherungsexperte</span>
    </h1>

    <div class="brand">
      <div class="brand__mark">
        <span class="brand__dot"></span>
        <span class="brand__name">Alpenblick</span>
      </div>
      <span class="brand__divider"></span>
      <div class="brand__text">
        <div class="brand__title">Vermögensberatung GmbH</div>
        <div class="brand__claim">Finanzieren, Versichern, Vorsorgen</div>
      </div>
    </div>

    <div class="services">
      <div class="service service--estate">
        <span class="service__icon">
          <svg width="34" height="34" viewBox="0 0 24 24" aria-hidden="true"><path d="M2 12 L12 3 L22 12 L19 12 L19 21 L5 21 L5 12 Z" fill="var(--icon-grey)"/><rect x="10" y="14" width="4" height="7" fill="var(--white)"/></svg>
        </span>
        <span>Real<br>Estate</span>
      </div>
      <span class="service__divider"></span>
      <div class="service service--financing">
        <span class="service__icon">
          <svg width="34" height="34" viewBox="0 0 24 24" aria-hidden="true"><path d="M9 2 H15 L13 6 H11 Z" fill="var(--icon-grey)"/><circle cx="12" cy="15" r="8" fill="var(--icon-grey)"/><text x="12" y="19" text-anchor="middle" font-size="11" font-weight="700" fill="var(--white)" font-family="Open Sans, sans-serif">$</text></svg>
        </span>
        <span>Business<br>Financing</span>
      </div>
      <span class="service__divider"></span>
      <div class="service service--insurance">
        <span class="service__icon">
          <svg width="34" height="34" viewBox="0 0 24 24" aria-hidden="true"><path d="M3 9 C6 3 18 3 21 9 Z" fill="var(--icon-grey)"/><circle cx="9" cy="13" r="2" fill="var(--icon-grey)"/><circle cx="15" cy="13" r="2" fill="var(--icon-grey)"/><rect x="7" y="16" width="4" height="6" rx="1.5" fill="var(--icon-grey)"/><rect x="13" y="16" width="4" height="6" rx="1.5" fill="var(--icon-grey)"/></svg>
        </span>
        <span>Independent<br>Insurance Advice</span>
      </div>
    </div>

    <div class="advisor-photo" role="img" aria-label="Portrait photo of the financial advisor in a dark suit and white shirt"></div>

    <div class="phone-pill">
      <svg width="22" height="38" viewBox="0 0 14 24" aria-hidden="true"><rect x="1" y="1" width="12" height="22" rx="2" fill="none" stroke="var(--white)" stroke-width="2"/><rect x="5" y="19" width="4" height="1.6" fill="var(--white)"/></svg>
      <span>0664/215 8840</span>
    </div>

    <div class="contacts">
      <span class="contact">
        <svg width="20" height="20" viewBox="0 0 24 24" aria-hidden="true"><circle cx="12" cy="12" r="10" fill="none" stroke="var(--ink)" stroke-width="2"/><ellipse cx="12" cy="12" rx="4.5" ry="10" fill="none" stroke="var(--ink)" stroke-width="1.6"/><line x1="2" y1="12" x2="22" y2="12" stroke="var(--ink)" stroke-width="1.6"/></svg>
        www.der-finanzpartner.at
      </span>
      <span class="contact">
        <svg width="24" height="18" viewBox="0 0 26 20" aria-hidden="true"><rect x="0" y="0" width="26" height="20" rx="2" fill="var(--ink)"/><path d="M2 3 L13 11 L24 3" fill="none" stroke="var(--white)" stroke-width="2"/></svg>
        office@der-finanzpartner.at
      </span>
    </div>
  </section>
</body>
</html>
```